Business card design for Brivo Engineering Tandem

We need a new business card design along with all the necessary to place an order. The company is Brivo Engineering Tandem and we recently updated our logo.

```html
<!DOCTYPE html>
<html lang="en">
<head>
<meta charset="utf-8">
<title>Brivo Engineering Tandem – Business Card</title>
<link rel="stylesheet" href="https://fonts.googleapis.com/css2?family=Kanit:wght@400;600&display=swap">
<style>
  :root {
    --page: #3a3b3d;
    --card: #1d1d1e;
    --accent: #e5c01f;
    --text: #f2f2f2;
    --brand-grey: #9b9b99;
    --sheen-top: #d2d2d2;
    --sheen-mid: #6b6a6a;
    --sheen-deep: #0a0a0a;
  }
  * { margin: 0; padding: 0; box-sizing: border-box; }
  html, body { width: 1200px; height: 1059px; overflow: hidden; }
  body {
    background: var(--page);
    font-family: "Kanit", sans-serif;
    position: relative;
  }
  .card {
    position: absolute;
    width: 690px;
    height: 394px;
    background: var(--card);
    border-radius: 22px;
    overflow: hidden;
    box-shadow: 0 12px 24px rgba(0,0,0,0.45);
  }
  .card--front { left: 256px; top: 100px; }
  .card--back  { left: 253px; top: 536px; }

  .decor {
    position: absolute;
    top: 0;
    height: 100%;
    background:
      linear-gradient(180deg, rgba(0,0,0,0) 55%, rgba(10,10,10,0.6) 100%),
      radial-gradient(ellipse 70% 60% at 50% 0%, var(--sheen-top) 0%, var(--sheen-mid) 35%, #2b2b2b 65%, var(--sheen-deep) 100%);
    -webkit-mask-image: linear-gradient(90deg, transparent 0%, #000 18%, #000 82%, transparent 100%);
            mask-image: linear-gradient(90deg, transparent 0%, #000 18%, #000 82%, transparent 100%);
  }
  .card--front .decor { left: 300px; width: 390px;
    -webkit-mask-image: linear-gradient(90deg, transparent 0%, #000 22%, #000 100%);
            mask-image: linear-gradient(90deg, transparent 0%, #000 22%, #000 100%); }
  .card--back .decor { left: 0; width: 450px;
    -webkit-mask-image: linear-gradient(90deg, #000 0%, #000 80%, transparent 100%);
            mask-image: linear-gradient(90deg, #000 0%, #000 80%, transparent 100%); }

  .brand {
    position: absolute;
    display: flex;
    align-items: center;
    gap: 12px;
    color: var(--brand-grey);
    font-weight: 600;
    text-transform: uppercase;
    letter-spacing: 0.04em;
    line-height: 1.1;
  }
  .brand__mark {
    width: 16px; height: 16px;
    background: var(--accent);
    flex: none;
  }
  .card--front .brand { left: 27px; top: 52px; font-size: 30px; }
  .card--back .brand {
    right: 28px; bottom: 40px; font-size: 22px;
    align-items: flex-start; text-align: right;
  }
  .card--back .brand__mark { margin-top: 5px; }

  .name-bar {
    position: absolute;
    left: 0; top: 154px;
    width: 13px; height: 53px;
    background: var(--accent);
  }
  .person {
    position: absolute;
    left: 27px; top: 145px;
  }
  .person__name {
    color: var(--accent);
    font-weight: 600;
    font-size: 32px;
    line-height: 1.2;
  }
  .person__role {
    color: var(--text);
    font-size: 18px;
    font-weight: 400;
    line-height: 1.3;
  }
  .address {
    position: absolute;
    left: 27px; top: 224px;
    color: var(--text);
    font-size: 19px;
    line-height: 28px;
    font-style: normal;
  }
  .contact {
    position: absolute;
    left: 27px; top: 290px;
    list-style: none;
    color: var(--text);
    font-size: 19px;
  }
  .contact__item {
    display: flex;
    align-items: center;
    gap: 9px;
    height: 27px;
  }
  .contact__icon { width: 15px; height: 15px; fill: var(--accent); flex: none; }
</style>
</head>
<body>

<section class="card card--front" aria-label="Business card front">
  <div class="decor" role="img" aria-label="Large metallic silver-to-black sheen decoration"></div>

  <div class="brand">
    <span class="brand__mark"></span>
    <span>Brivo Engineering Tandem</span>
  </div>

  <div class="name-bar"></div>
  <div class="person">
    <h1 class="person__name">DANIEL HARTLEY</h1>
    <p class="person__role">Managing Director</p>
  </div>

  <address class="address">
    Brivo Engineering Tandem<br>
    24 Fenwick Road, Kettering NN15 6XT
  </address>

  <ul class="contact">
    <li class="contact__item">
      <svg class="contact__icon" viewBox="0 0 16 16" aria-hidden="true"><path d="M1 6c0-2 3-3.5 7-3.5S15 4 15 6v1.5h-3.5V6H4.5v1.5H1z M3.5 9 5 7.5h6L12.5 9v5h-9z"/></svg>
      <span>01536 402871</span>
    </li>
    <li class="contact__item">
      <svg class="contact__icon" viewBox="0 0 16 16" aria-hidden="true"><path d="M1 3h14v1.2L8 9 1 4.2z M1 5.8 8 10.6l7-4.8V13H1z"/></svg>
      <span>sales@brivoengineering.co.uk</span>
    </li>
    <li class="contact__item">
      <svg class="contact__icon" viewBox="0 0 16 16" aria-hidden="true"><circle cx="8" cy="8" r="7"/></svg>
      <span>www.brivoengineering.co.uk</span>
    </li>
  </ul>
</section>

<section class="card card--back" aria-label="Business card back">
  <div class="decor" role="img" aria-label="Large metallic silver-to-black sheen decoration"></div>
  <div class="brand">
    <span class="brand__mark"></span>
    <span>Brivo Engineering<br>Tandem</span>
  </div>
</section>

</body>
</html>
```